Oil and Gas Exploration and Production company needs a business card design

We need a business card design using our logo and colors in the logo. We want a mainstream design.

```html
<!DOCTYPE html>
<html lang="en">
<head>
<meta charset="utf-8">
<title>Corvo Oil &amp; Gas — Business Card</title>
<link rel="stylesheet" href="https://fonts.googleapis.com/css2?family=Libre+Baskerville:wght@700&family=Mulish:wght@400;800&display=swap">
<style>
  :root {
    --backdrop: #e4e4e4;
    --card-black: #0b0b0b;
    --pattern-tone: #1c1c1c;
    --panel-white: #f7f7f5;
    --gold: #c8962a;
    --ink: #111111;
    --text-light: #f2f2f2;
  }
  html, body {
    margin: 0;
    padding: 0;
    width: 1200px;
    height: 957px;
    overflow: hidden;
    background: var(--backdrop);
  }
  .canvas {
    position: relative;
    width: 1200px;
    height: 957px;
  }
  .business-card {
    position: absolute;
    left: 100px;
    top: 192px;
    width: 1000px;
    height: 572px;
    background: var(--card-black);
    overflow: hidden;
    box-shadow: 0 18px 40px rgba(0,0,0,0.18);
  }
  .card-pattern {
    position: absolute;
    inset: 0;
    background: radial-gradient(circle at 62% 62%, var(--pattern-tone) 0%, var(--card-black) 70%);
  }
  .logo-panel {
    position: absolute;
    left: 265px;
    top: 0;
    width: 390px;
    height: 228px;
    background: var(--panel-white);
    border: 9px solid var(--gold);
    border-top: none;
    border-radius: 0 0 56px 56px;
    box-sizing: border-box;
    display: flex;
    align-items: center;
    justify-content: center;
    gap: 14px;
    padding: 0 24px;
  }
  .logo-mark {
    flex-shrink: 0;
    width: 28px;
    height: 28px;
    border-radius: 50%;
    background: var(--ink);
  }
  .logo-name {
    font-family: "Mulish", sans-serif;
    font-weight: 800;
    font-size: 34px;
    color: var(--ink);
    white-space: nowrap;
  }
  .card-details {
    position: absolute;
    left: 300px;
    width: 620px;
    top: 262px;
    text-align: center;
  }
  .holder-name {
    font-family: "Libre Baskerville", serif;
    font-weight: 700;
    font-size: 40px;
    color: var(--gold);
    margin: 0;
    line-height: 1.1;
  }
  .holder-role {
    font-family: "Mulish", sans-serif;
    font-weight: 400;
    font-size: 32px;
    color: var(--text-light);
    margin: 2px 0 0;
    letter-spacing: 0.5px;
  }
  .contact-lines {
    font-family: "Mulish", sans-serif;
    font-weight: 400;
    font-size: 28px;
    color: var(--text-light);
    margin: 58px 0 0;
    line-height: 1.45;
    white-space: nowrap;
  }
  .contact-lines p { margin: 0; }
</style>
</head>
<body>
<main class="canvas">
  <section class="business-card">
    <div class="card-pattern" role="img" aria-label="Faint dark mandala ornament pattern across the card background"></div>
    <div class="logo-panel">
      <span class="logo-mark"></span>
      <span class="logo-name">Corvo Oil &amp; Gas</span>
    </div>
    <div class="card-details">
      <h1 class="holder-name">Your Name</h1>
      <p class="holder-role">OWNER</p>
      <div class="contact-lines">
        <p>(555) 010-0199 | hello@corvo-energy.com</p>
        <p>www.corvo-energy.com</p>
      </div>
    </div>
  </section>
</main>
</body>
</html>
```